Business card design for new eCommerce site focusing on integrity and strong businsess tactics

We need a business card that will stand out and be memorable. Something with color that matches our company logo colors. Think high end version of Pactivo. There are 2 logos provided. The parent company is called Amber Ledge Partners and we are presenting a new and very exciting eCommerce site called BrightHarborTrade.example.

Target Market(s)

Our target markets are in the Activities, Food and Beverage, Health and Beauty

Industry/Entity Type

Marketing

Contact Information for Business Card

We have 4 members that need cards...I will provide all info to the winner of the design contest
Business Address is
4870 West 63rd Avenue, Suite C207
Phoenix AZ 85731

Font styles to use
Serif
Sans Serif

Colors

Designer to choose colors to be used in the design.

Requirements
Must have
• The card must be memorable...should be unique in design but must exude integrity and be playful .
• I have provided several colors or our parent company...please feel free to use which ever
Nice to have
• I will leave this up to you. Feel free to use other images of your choosing that wraps around our client.....Activities, Dining, Health, Beauty
Should not have
• just dont be boring

```html
<!DOCTYPE html>
<html lang="en">
<head>
<meta charset="utf-8">
<title>BrightHarborTrade.example – Business Card</title>
<link rel="stylesheet" href="https://fonts.googleapis.com/css2?family=Jost:wght@300;400;500;600&display=swap">
<style>
  :root {
    --page-bg: #ece9e4;
    --card-white: #f7f7f7;
    --brand-blue: #2b7fb3;
    --brand-green: #7dc242;
    --wave-grey: #5d5f61;
    --ink-dark: #4a4c4e;
    --ink-light: #ffffff;
    --card-shadow: rgba(0, 0, 0, 0.28);
  }
  * { box-sizing: border-box; margin: 0; padding: 0; }
  html, body {
    width: 1200px; height: 960px; overflow: hidden;
    background: var(--page-bg);
    font-family: "Jost", "Futura", sans-serif;
  }
  .canvas { position: relative; width: 1200px; height: 960px; }

  .card {
    position: absolute; width: 600px; height: 342px;
    border-radius: 22px; overflow: hidden;
    box-shadow: 3px 4px 8px var(--card-shadow);
  }
  .card--front { left: 302px; top: 131px; background: var(--card-white); }
  .card--back  { left: 299px; top: 490px; background: var(--brand-blue); }

  .front-wave { position: absolute; inset: 0; }

  .brand-lockup {
    position: absolute; left: 88px; top: 58px;
    display: flex; align-items: center; gap: 16px;
  }
  .brand-mark {
    width: 44px; height: 44px; border-radius: 50%;
    background: var(--brand-green); flex: none;
  }
  .brand-name {
    font-size: 30px; font-weight: 500; color: var(--brand-blue);
    line-height: 1;
  }
  .brand-tagline {
    margin-top: 8px; font-size: 15px; font-weight: 400;
    letter-spacing: 1.2px; color: var(--ink-dark);
  }

  .holder {
    position: absolute; right: 322px; top: 226px;
    text-align: right; color: var(--ink-light);
    font-size: 14px; line-height: 19px; font-weight: 400;
  }
  .holder__name {
    font-size: 21px; line-height: 24px; color: var(--brand-green);
    font-weight: 400; text-transform: uppercase;
  }
  .holder__title { font-size: 15px; margin-bottom: 3px; }

  .divider {
    position: absolute; left: 296px; top: 226px;
    width: 2px; height: 82px; background: var(--ink-light);
  }

  .contact-list {
    position: absolute; left: 316px; top: 230px;
    list-style: none; color: var(--ink-light);
    font-size: 14.5px; line-height: 19.5px;
  }
  .contact-list li { display: flex; align-items: center; gap: 9px; }
  .contact-list svg { width: 12px; height: 12px; fill: var(--brand-green); flex: none; }

  .back-lockup {
    position: absolute; inset: 0;
    display: flex; flex-direction: column; align-items: center; justify-content: center;
    gap: 34px; color: var(--ink-light);
  }
  .back-mark {
    width: 96px; height: 96px; border-radius: 50%;
    border: 6px solid var(--ink-light);
  }
  .back-name { font-size: 36px; font-weight: 600; line-height: 1; }
</style>
</head>
<body>
<main class="canvas">

  <section class="card card--front" aria-label="Business card front">
    <svg class="front-wave" viewBox="0 0 600 342" width="600" height="342" aria-hidden="true">
      <path d="M0,176 C120,206 250,206 380,176 C470,156 540,168 600,208 L600,342 L0,342 Z" fill="var(--brand-blue)"/>
      <path d="M0,172 C120,200 250,198 380,168 C440,155 480,156 520,164" fill="none" stroke="var(--wave-grey)" stroke-width="4"/>
      <path d="M330,178 C420,150 510,150 600,204" fill="none" stroke="var(--brand-green)" stroke-width="4"/>
      <path d="M0,178 C120,208 250,208 380,178 C470,158 540,170 600,210" fill="none" stroke="#ffffff" stroke-width="2"/>
    </svg>

    <div class="brand-lockup">
      <span class="brand-mark" aria-hidden="true"></span>
      <div>
        <div class="brand-name">BrightHarborTrade.example</div>
        <div class="brand-tagline">Activities-Dining-Health-Beauty</div>
      </div>
    </div>

    <div class="holder">
      <div class="holder__name">Dana Whitfield</div>
      <div class="holder__title">CEO/FOUNDER</div>
      <div>4870 West 63rd Avenue</div>
      <div>Suite C207, Phoenix AZ 85731</div>
    </div>

    <div class="divider" aria-hidden="true"></div>

    <ul class="contact-list">
      <li><svg viewBox="0 0 24 24" aria-hidden="true"><path d="M6.6 10.8a15.1 15.1 0 0 0 6.6 6.6l2.2-2.2a1 1 0 0 1 1-.25 11.4 11.4 0 0 0 3.6.57 1 1 0 0 1 1 1V20a1 1 0 0 1-1 1A17 17 0 0 1 3 4a1 1 0 0 1 1-1h3.5a1 1 0 0 1 1 1c0 1.25.2 2.45.57 3.57a1 1 0 0 1-.25 1z"/></svg>602 555 0148</li>
      <li><svg viewBox="0 0 24 24" aria-hidden="true"><path d="M7 1h10a2 2 0 0 1 2 2v18a2 2 0 0 1-2 2H7a2 2 0 0 1-2-2V3a2 2 0 0 1 2-2zm0 3v14h10V4zm5 15.5a1.2 1.2 0 1 0 0 2.4 1.2 1.2 0 0 0 0-2.4z"/></svg>602 555 0193</li>
      <li><svg viewBox="0 0 24 24" aria-hidden="true"><path d="M2 5h20v14H2zm2 2v.5l8 5 8-5V7zm0 2.8V17h16V9.8l-8 5z"/></svg>dana@brightharbortrade.example</li>
      <li><svg viewBox="0 0 24 24" aria-hidden="true"><path d="M12 2a10 10 0 1 0 0 20 10 10 0 0 0 0-20zm-1 17.9A8 8 0 0 1 4.1 11H7c0 3 1.5 6 4 8.9zM4.1 13zM13 4.1A8 8 0 0 1 19.9 11H17c0-2.7-1.4-5.1-4-6.9zm-2 0C8.6 5.9 7.2 8.3 7 11h10c-.2-2.7-1.6-5.1-4-6.9zM13 19.9c2.4-2.9 3.8-5.9 4-8.9h2.9a8 8 0 0 1-6.9 8.9z"/></svg>www.brightharbortrade.example</li>
    </ul>
  </section>

  <section class="card card--back" aria-label="Business card back">
    <div class="back-lockup">
      <span class="back-mark" aria-hidden="true"></span>
      <div class="back-name">Amber Ledge Partners</div>
    </div>
  </section>

</main>
</body>
</html>
```